Carpentry framing business card and logo design

We need a logo that works well with baseball caps, tee shirts and sweat shirts. We are a carpentry framing company specializing in apartment complexes and large residential communities. We work in what is known as the tri state area southeastern Pennsylvania , New Jersey and northern Delaware . We would like to see die signs using the old English letter M and royal blue colors. Also we stress OSHA compliance and safety.

Industry/Entity Type

Residential

Contact Information for Business Card

Valdrick Construction Co Inc
4870 Quillford Lane
Hollin KV 55087
Dale Valdrick
dale1valdrick@norvexmail.com
555-815-0926

```html
<!DOCTYPE html>
<html lang="en">
<head>
<meta charset="utf-8">
<title>Valdrick Construction Co Inc – Business Card</title>
<link rel="stylesheet" href="https://fonts.googleapis.com/css2?family=Cinzel:wght@400;500&family=Arimo:wght@400&display=swap">
<style>
  :root {
    --navy: #2b2a7a;
    --red: #e0301e;
    --card: #ffffff;
    --backdrop: #d9d9d9;
  }
  * { margin: 0; padding: 0; box-sizing: border-box; }
  html, body {
    width: 1200px; height: 848px; overflow: hidden;
    background: var(--backdrop);
  }
  .card {
    position: absolute;
    left: 75px; top: 124px;
    width: 1050px; height: 600px;
    background: var(--card);
    border-radius: 28px;
    box-shadow: 0 6px 24px rgba(0,0,0,.18);
    overflow: hidden;
  }
  .brand {
    position: absolute;
    left: 70px; top: 92px;
    display: flex; align-items: center; gap: 18px;
  }
  .brand-square {
    width: 30px; height: 30px;
    background: var(--red);
    flex: none;
  }
  .brand-name {
    font-family: "Cinzel", serif;
    font-weight: 500;
    font-size: 40px;
    line-height: 1.1;
    color: var(--navy);
  }
  .divider {
    position: absolute;
    left: 0; top: 300px;
    width: 560px; height: 1.5px;
    background: var(--navy);
  }
  .person-name {
    position: absolute;
    left: 585px; top: 272px;
    font-family: "Cinzel", serif;
    font-weight: 400;
    font-size: 40px;
    color: var(--red);
    white-space: nowrap;
  }
  .contact {
    font-family: "Arimo", sans-serif;
    font-style: normal;
    font-size: 26px;
    color: var(--navy);
    line-height: 1.35;
  }
  .address {
    position: absolute;
    left: 700px; top: 368px;
    display: flex; gap: 14px; align-items: flex-start;
  }
  .address .icon { margin-top: 14px; }
  .reach {
    position: absolute;
    left: 70px; top: 468px;
    list-style: none;
  }
  .reach li { display: flex; align-items: center; gap: 16px; margin-bottom: 6px; }
  .icon { width: 24px; height: 24px; flex: none; }
</style>
</head>
<body>
  <main class="card">
    <div class="brand">
      <span class="brand-square"></span>
      <span class="brand-name">Valdrick<br>Construction Co Inc</span>
    </div>

    <span class="divider"></span>
    <h1 class="person-name">Dale Valdrick</h1>

    <address class="contact address">
      <svg class="icon" viewBox="0 0 24 24" aria-hidden="true">
        <path fill="var(--red)" d="M12 1a8 8 0 0 0-8 8c0 6 8 14 8 14s8-8 8-14a8 8 0 0 0-8-8zm0 11a3 3 0 1 1 0-6 3 3 0 0 1 0 6z"/>
      </svg>
      <span>4870 Quillford Lane<br>Hollin KV 55087</span>
    </address>

    <ul class="contact reach">
      <li>
        <svg class="icon" viewBox="0 0 24 24" aria-hidden="true">
          <path fill="var(--red)" d="M6.6 10.8a15 15 0 0 0 6.6 6.6l2.2-2.2c.3-.3.7-.4 1-.2 1.1.4 2.3.6 3.6.6.6 0 1 .4 1 1V20c0 .6-.4 1-1 1A17 17 0 0 1 3 4c0-.6.4-1 1-1h3.5c.6 0 1 .4 1 1 0 1.3.2 2.5.6 3.6.1.3 0 .7-.2 1z"/>
        </svg>
        <span>555-815-0926</span>
      </li>
      <li>
        <svg class="icon" viewBox="0 0 24 24" aria-hidden="true">
          <rect x="2" y="5" width="20" height="14" fill="var(--red)"/>
          <path d="M2 5l10 8 10-8M2 19l7-6M22 19l-7-6" stroke="#fff" stroke-width="1.6" fill="none"/>
        </svg>
        <span>dale1valdrick@norvexmail.com</span>
      </li>
    </ul>
  </main>
</body>
</html>
```